Corportate Power Point Template

We need a corporate PPT Design for our startup Big Data company.

Basically, our company will ingest, analyze and generate dynamic Dashboards with data consumed from different sources like Social Networks, Enterprise Legacy Systems such as e-Commerce, ERP, CRM and others.

Company is headquartered in Brazil, but will have a global presence.

Industry/Entity Type

It Company

```html
<!DOCTYPE html>
<html lang="en">
<head>
<meta charset="utf-8">
<title>Vantora Data – Closing Slide</title>
<link href="https://fonts.googleapis.com/css2?family=Open+Sans:wght@400;600&family=Saira+Semi+Condensed:wght@400;500;600&display=swap" rel="stylesheet">
<style>
  :root {
    --orange: #f26a21;
    --orange-soft: #f58a4a;
    --ink: #1d1d1d;
    --ink-muted: #3a3a3a;
    --paper: #fdfbf9;
    --divider: #d8d4d0;
    --grid-tone: #ecebea;
    --glow: #fbe3cf;
  }
  * { margin: 0; padding: 0; box-sizing: border-box; }
  html, body { width: 1200px; height: 900px; overflow: hidden; }
  body { background: var(--paper); font-family: "Open Sans", sans-serif; color: var(--ink); }

  .slide {
    position: relative;
    width: 1200px;
    height: 900px;
    overflow: hidden;
    background:
      radial-gradient(ellipse 620px 420px at 220px 80px, var(--glow) 0%, rgba(251,227,207,0.35) 45%, rgba(253,251,249,0) 75%),
      linear-gradient(180deg, rgba(253,251,249,0) 60%, #fff 100%),
      var(--paper);
  }

  .backdrop-texture {
    position: absolute;
    top: 0;
    right: 0;
    width: 360px;
    height: 900px;
    background: linear-gradient(90deg, rgba(236,235,234,0) 0%, var(--grid-tone) 60%, rgba(236,235,234,0.6) 100%);
    opacity: 0.55;
  }

  .brand {
    position: absolute;
    left: 98px;
    top: 432px;
    display: flex;
    align-items: center;
    gap: 14px;
  }
  .brand-mark {
    width: 30px;
    height: 30px;
    background: var(--orange);
  }
  .brand-name {
    font-family: "Open Sans", sans-serif;
    font-weight: 600;
    font-size: 54px;
    line-height: 1;
    color: var(--orange);
    letter-spacing: -0.5px;
  }

  .presenter {
    position: absolute;
    left: 116px;
    top: 538px;
    font-family: "Saira Semi Condensed", sans-serif;
    font-size: 25px;
    color: var(--ink-muted);
  }
  .presenter-name { color: var(--orange); font-weight: 500; }

  .divider {
    position: absolute;
    left: 589px;
    top: 278px;
    width: 1px;
    height: 406px;
    background: linear-gradient(180deg, rgba(216,212,208,0) 0%, var(--divider) 20%, var(--divider) 80%, rgba(216,212,208,0) 100%);
  }

  .project {
    position: absolute;
    left: 645px;
    top: 326px;
    width: 460px;
  }
  .project-title {
    font-family: "Saira Semi Condensed", sans-serif;
    font-weight: 500;
    font-size: 43px;
    line-height: 1.1;
    color: var(--orange);
  }
  .project-summary {
    margin-top: 10px;
    font-size: 20px;
    line-height: 33px;
    color: var(--ink);
  }

  .contact-list {
    list-style: none;
    margin-top: 34px;
  }
  .contact-item {
    display: flex;
    align-items: center;
    gap: 16px;
    height: 34px;
    margin-bottom: 30px;
    font-size: 21px;
    color: var(--ink);
  }
  .contact-icon { width: 34px; height: 34px; flex: none; }
</style>
</head>
<body>
  <main class="slide">
    <div class="backdrop-texture" role="img" aria-label="Faint grey tiled texture fading in from the right edge"></div>

    <div class="brand">
      <span class="brand-name">Vantora Data</span>
      <span class="brand-mark"></span>
    </div>

    <p class="presenter">Persentatator Name : <span class="presenter-name">Marcos Vilela</span></p>

    <div class="divider"></div>

    <section class="project">
      <h1 class="project-title">Project Title Here</h1>
      <p class="project-summary">Contact Details line here Contact Details line here, Contact Details line here</p>

      <ul class="contact-list">
        <li class="contact-item">
          <svg class="contact-icon" viewBox="0 0 34 34" aria-hidden="true">
            <circle cx="17" cy="17" r="17" fill="var(--orange)"/>
            <path d="M12.5 9.5c.8-.5 1.6-.3 2 .4l1.6 2.6c.4.7.2 1.4-.4 1.9l-1 .8c.7 1.8 2.2 3.5 4.1 4.5l.9-1c.5-.6 1.3-.7 1.9-.3l2.6 1.6c.7.4.9 1.3.4 2l-1 1.5c-.8 1.1-2.3 1.4-3.6.8-4.2-1.9-7.3-5.2-8.9-9.4-.5-1.3-.1-2.8 1-3.6z" fill="#fff"/>
          </svg>
          <span>01 5550 238190</span>
        </li>
        <li class="contact-item">
          <svg class="contact-icon" viewBox="0 0 34 34" aria-hidden="true">
            <circle cx="17" cy="17" r="17" fill="var(--orange)"/>
            <rect x="9" y="11.5" width="16" height="11" rx="1" fill="none" stroke="#fff" stroke-width="1.8"/>
            <path d="M9.5 12.5l7.5 6 7.5-6" fill="none" stroke="#fff" stroke-width="1.8" stroke-linejoin="round"/>
          </svg>
          <span>info@vantoradata.com</span>
        </li>
        <li class="contact-item">
          <svg class="contact-icon" viewBox="0 0 34 34" aria-hidden="true">
            <circle cx="17" cy="17" r="17" fill="var(--orange)"/>
            <path d="M9 11l2.8 12h1.4L17 14l3.8 9h1.4L25 11" fill="none" stroke="#fff" stroke-width="2.2" stroke-linejoin="round" stroke-linecap="round"/>
          </svg>
          <span>www.vantoradata.com</span>
        </li>
      </ul>
    </section>
  </main>
</body>
</html>
```